Timber Crest Construction Needs business card

Hey we are in need of business card designs. I have upload our logo as a guideline, but free feel to run with it or come up with something unique.
Pls have fun with it and be creative. the name says it all!
i will give some directions after i see a few entries..
Updates
Logo source file has been uploaded..
Hey because of the logo is so colourful already.
Can we have a few submissions with less colour.
Also we are looking for clever/hidden/descriptive business card.

```html
<!DOCTYPE html>
<html lang="en">
<head>
<meta charset="utf-8">
<title>Timber Crest Construction – Business Card</title>
<link rel="stylesheet" href="https://fonts.googleapis.com/css2?family=Arimo&family=Syncopate:wght@700&display=swap">
<style>
  :root {
    --backdrop: #ffcc00;
    --edge: #4a4a4a;
    --card: #ffffff;
    --pattern-tone: #c2c2c2;
    --accent-red: #e8161b;
    --brand-slate: #667b82;
  }
  html, body {
    margin: 0;
    padding: 0;
    width: 1200px;
    height: 1200px;
    overflow: hidden;
    background: var(--backdrop);
  }
  .stage {
    display: block;
    width: 1200px;
    height: 1200px;
  }
  .backdrop { fill: var(--backdrop); stroke: var(--edge); stroke-width: 2; }
  .card { fill: var(--card); stroke: var(--edge); stroke-width: 1.5; }
  .border-pattern { fill: var(--pattern-tone); }
  .feature-list {
    font-family: "Arimo", Arial, sans-serif;
    font-size: 20px;
    fill: var(--accent-red);
  }
  .contact-line {
    font-family: "Syncopate", "Arial Black", sans-serif;
    font-weight: 700;
    font-size: 15px;
    letter-spacing: 1.5px;
    fill: var(--accent-red);
  }
  .brand-name {
    font-family: "Arimo", Arial, sans-serif;
    fill: var(--brand-slate);
  }
  .brand-name .primary { font-size: 38px; letter-spacing: 0.5px; }
  .brand-name .secondary { font-size: 12px; letter-spacing: 2px; }
  .brand-mark { fill: var(--brand-slate); }
</style>
</head>
<body>
<svg class="stage" viewBox="0 0 1125 1125" xmlns="http://www.w3.org/2000/svg">
  <rect class="backdrop" x="1" y="1" width="1123" height="1123"/>

  <!-- Card back: feature list -->
  <g class="card-back" transform="translate(96 208) rotate(-14.85)">
    <rect class="card" x="0" y="0" width="663" height="380"/>
    <path class="border-pattern" role="img" aria-label="Grey and white checkered border framing the card"
          fill-rule="evenodd"
          d="M0 0 H663 V380 H0 Z M110 72 V270 H553 V72 Z"/>
    <text class="feature-list">
      <tspan x="240" y="172">Work Features</tspan>
      <tspan x="241" y="200">Work specialty</tspan>
      <tspan x="246" y="228">Contact Details</tspan>
    </text>
  </g>

  <!-- Card front: brand and contact -->
  <g class="card-front" transform="translate(314 637) rotate(-5.18)">
    <rect class="card" x="0" y="0" width="665" height="380"/>
    <path class="border-pattern" role="img" aria-label="Stepped grey and white checkered blocks along the lower edge"
          d="M0 115 H38 V182 H115 V300 H230 V345 H265 V330 H360 V290 H500 V235 H565 V190 H620 V150 H665 V380 H0 Z"/>

    <text class="contact-line" x="424" y="40">Proprietor Name</text>
    <text class="contact-line" x="424" y="60">000000000</text>

    <rect class="brand-mark" x="314" y="92" width="38" height="38"/>
    <text class="brand-name" text-anchor="middle">
      <tspan class="primary" x="333" y="178">TIMBER CREST</tspan>
      <tspan class="secondary" x="333" y="196">CONSTRUCTION</tspan>
    </text>

    <text class="contact-line" x="333" y="236" text-anchor="middle">Email, Address</text>
  </g>
</svg>
</body>
</html>
```